Quorvix banner ad for roofing company

We need an ad created for a Quorvix banner advertising campaign for a UK based roofing company.

The design should have a large photograph on the background (see attached).
The design should have our Glimmerdew rating (5 stars).
There should be a large text header at the top which reads "Your local roofing experts"

The following services should be listed:
- New roofs
- General roof repairs
- Drone surveys
- Single ply roofing
- Steel cladding
- Asbestos removal

The company logo needs to be visible (attached). Also the company telephone number 020 7946 0321 and website www.brinthoveroofing.com

The advert needs to be horizontal/landscape design. For full spec, please see here: https://promo.quorvix.com/advertiser-help/guides/ad-formats/single-photo-ads

Size required: 1.91:1 - 1200 x 628 pixels

```html
<!DOCTYPE html>
<html lang="en">
<head>
<meta charset="utf-8">
<title>Brinthove Roofing – Banner</title>
<link rel="stylesheet" href="https://fonts.googleapis.com/css2?family=Outfit:wght@300;400;600;700&display=swap">
<style>
  :root {
    --navy: #11497b;
    --navy-deep: #0b3a64;
    --cyan: #00aedb;
    --cyan-soft: #8fdcf0;
    --halo: #c5ecf7;
    --white: #ffffff;
    --frame: #c9c9c9;
  }
  * { margin: 0; padding: 0; box-sizing: border-box; }
  html, body { width: 1200px; height: 1200px; overflow: hidden; background: var(--white); }
  body { position: relative; font-family: "Outfit", sans-serif; }

  .banner {
    position: absolute; left: 123px; top: 362px;
    width: 955px; height: 499px;
    border: 1px solid var(--frame);
    overflow: hidden; background: var(--white);
  }
  .banner-shapes { position: absolute; inset: 0; }

  .brand {
    position: absolute; left: 46px; top: 24px;
    display: flex; align-items: center; gap: 10px;
  }
  .brand-dot { width: 32px; height: 32px; border-radius: 50%; background: var(--navy); }
  .brand-name { font-size: 34px; font-weight: 700; color: var(--navy); letter-spacing: -0.5px; }

  .headline {
    position: absolute; left: 44px; top: 128px;
    font-size: 49px; font-weight: 700; line-height: 51px;
    color: var(--cyan-soft); letter-spacing: -0.5px;
    text-shadow: 2px 3px 0 var(--white);
  }

  .services {
    position: absolute; left: 44px; top: 264px;
    list-style: none; color: var(--white);
    font-size: 23px; font-weight: 300; line-height: 33.7px;
  }
  .services li::before { content: "•"; font-size: 15px; margin-right: 8px; vertical-align: 3px; }

  .rating {
    position: absolute; left: 371px; top: 288px;
    width: 182px; height: 182px; border-radius: 50%;
    background: var(--navy-deep); border: 3px solid var(--cyan);
    display: flex; flex-direction: column; align-items: center;
    color: var(--white);
  }
  .rating-label { margin-top: 38px; font-size: 19px; font-weight: 400; letter-spacing: 1px; }
  .rating-stars { display: flex; gap: 3px; margin-top: 10px; }
  .rating-stars span {
    width: 25px; height: 25px; background: var(--cyan);
    display: flex; align-items: center; justify-content: center;
  }
  .rating-on { font-size: 13px; margin-top: 2px; }
  .rating-source { display: flex; align-items: center; gap: 5px; font-size: 16px; font-weight: 400; margin-top: 2px; }
  .rating-source i { width: 12px; height: 12px; border-radius: 50%; background: var(--cyan); display: block; }

  .contact {
    position: absolute; left: 592px; top: 420px;
    color: var(--white); font-weight: 600;
  }
  .contact-row { display: flex; align-items: center; gap: 9px; height: 29px; }
  .contact-row svg { flex: none; }
  .contact-phone { font-size: 26px; }
  .contact-web { font-size: 24px; letter-spacing: 0.5px; }
</style>
</head>
<body>
<div class="banner">
  <svg class="banner-shapes" width="955" height="499" viewBox="0 0 955 499">
    <defs>
      <linearGradient id="aerialTones" x1="0" y1="0" x2="1" y2="1">
        <stop offset="0" stop-color="#6f8a5a"/>
        <stop offset="0.4" stop-color="#9aa39a"/>
        <stop offset="0.7" stop-color="#b89a7c"/>
        <stop offset="1" stop-color="#5f7d4c"/>
      </linearGradient>
    </defs>
    <path d="M0,87 L330,87 Q400,87 455,115 L455,499 L0,499 Z" fill="var(--navy)"/>
    <path d="M505,0 C440,45 408,120 416,180" fill="none" stroke="var(--halo)" stroke-width="6"/>
    <path role="img" aria-label="Aerial photograph of a campus of flat-roofed residential blocks with grey roofs, lawns and paths"
          d="M521,0 C455,40 420,120 430,180 C440,260 500,360 590,399 L955,399 L955,0 Z" fill="url(#aerialTones)"/>
    <path d="M590,399 L955,399 L955,499 L520,499 C545,460 565,425 590,399 Z" fill="var(--cyan)"/>
  </svg>

  <div class="brand">
    <span class="brand-dot"></span>
    <span class="brand-name">brinthoveroofing</span>
  </div>

  <h1 class="headline">Your local<br>roofing experts</h1>

  <ul class="services">
    <li>New roofs</li>
    <li>General roof repairs</li>
    <li>Drone surveys</li>
    <li>Single ply roofing</li>
    <li>Steel cladding</li>
    <li>Asbestos removal</li>
  </ul>

  <div class="rating">
    <span class="rating-label">Excellent</span>
    <div class="rating-stars">
      <span><svg width="17" height="17" viewBox="0 0 24 24"><path d="M12 2l2.9 6.9 7.1.6-5.4 4.7 1.7 7.3L12 17.7 5.7 21.5l1.7-7.3L2 9.5l7.1-.6z" fill="#fff"/></svg></span>
      <span><svg width="17" height="17" viewBox="0 0 24 24"><path d="M12 2l2.9 6.9 7.1.6-5.4 4.7 1.7 7.3L12 17.7 5.7 21.5l1.7-7.3L2 9.5l7.1-.6z" fill="#fff"/></svg></span>
      <span><svg width="17" height="17" viewBox="0 0 24 24"><path d="M12 2l2.9 6.9 7.1.6-5.4 4.7 1.7 7.3L12 17.7 5.7 21.5l1.7-7.3L2 9.5l7.1-.6z" fill="#fff"/></svg></span>
      <span><svg width="17" height="17" viewBox="0 0 24 24"><path d="M12 2l2.9 6.9 7.1.6-5.4 4.7 1.7 7.3L12 17.7 5.7 21.5l1.7-7.3L2 9.5l7.1-.6z" fill="#fff"/></svg></span>
      <span><svg width="17" height="17" viewBox="0 0 24 24"><path d="M12 2l2.9 6.9 7.1.6-5.4 4.7 1.7 7.3L12 17.7 5.7 21.5l1.7-7.3L2 9.5l7.1-.6z" fill="#fff"/></svg></span>
    </div>
    <span class="rating-on">on</span>
    <span class="rating-source"><i></i>Glimmerdew</span>
  </div>

  <div class="contact">
    <div class="contact-row contact-phone">
      <svg width="24" height="24" viewBox="0 0 24 24"><circle cx="12" cy="12" r="12" fill="#fff"/><path d="M8.2 6.5l1.8-.4 1.2 2.8-1.3 1c.6 1.4 1.6 2.5 3 3.2l1-1.3 2.8 1.2-.4 1.8c-.2.6-.8 1-1.4.9-4-.6-7-3.6-7.6-7.6-.1-.7.3-1.3.9-1.6z" fill="none" stroke="var(--cyan)" stroke-width="1.4" stroke-linejoin="round"/></svg>
      <span>020 7946 0321</span>
    </div>
    <div class="contact-row contact-web">
      <svg width="24" height="24" viewBox="0 0 24 24"><circle cx="12" cy="12" r="12" fill="#fff"/><path d="M17.5 6.5L6 11l4.6 1.9L12.5 17.5z M10.6 12.9l6.9-6.4" fill="none" stroke="var(--cyan)" stroke-width="1.4" stroke-linejoin="round"/></svg>
      <span>www.brinthoveroofing.com</span>
    </div>
  </div>
</div>
</body>
</html>
```